Velvet Riot Rising Line of Sparkling Wine & Spirits

Back info: Nora Beth Quill Owner 555-318-4402 1480 E. Harlow Ave, Bldg. 2, & 3, Harrowvale Ca. 95871
Fine Vintages & Collectibles www.velvetriotrising.com
Ok I have uploaded the winning design. The color that I am after is the Fushia, Raspberry, Red, Matte Satin Matalic Finish. With a 24 Karet Gold color Foil. The Bottle is on the top row and it's the 2nd Bottle in. That is the Color that I want. This is the style of font. Make sure that you put what we're advertising. Good Luck to you all. Warmest regards, Nora
21 & up UniSex
Sparkling Wine and Memorabilia
there listed up above.....

```html
<!DOCTYPE html>
<html lang="en">
<head>
<meta charset="utf-8">
<title>Velvet Riot Rising – Business Card</title>
<link rel="stylesheet" href="https://fonts.googleapis.com/css2?family=Cinzel:wght@400;600&display=swap">
<style>
  :root {
    --backdrop: #2e2f31;
    --fuchsia-light: #e3168f;
    --fuchsia-mid: #c81480;
    --fuchsia-deep: #8a0f4a;
    --gold: #d8b256;
    --gold-deep: #b8871f;
    --paper-white: #fbeef5;
  }
  html, body {
    margin: 0;
    padding: 0;
    width: 1200px;
    height: 1200px;
    overflow: hidden;
    background: var(--backdrop);
  }
  .canvas {
    position: relative;
    width: 1200px;
    height: 1200px;
    font-family: "Cinzel", serif;
  }
  .card {
    position: absolute;
    left: 180px;
    width: 840px;
    height: 480px;
    border-radius: 42px;
    background: radial-gradient(ellipse 70% 90% at 45% 45%, var(--fuchsia-light) 0%, var(--fuchsia-mid) 55%, var(--fuchsia-deep) 100%);
    box-shadow: 0 4px 0 var(--gold-deep), 0 18px 30px rgba(0,0,0,0.45);
    overflow: hidden;
  }
  .card--info { top: 70px; }
  .card--brand { top: 640px; }

  .card--info .gold-edge {
    position: absolute;
    left: 0; right: 0; bottom: 0;
    height: 10px;
    background: linear-gradient(90deg, var(--gold-deep), var(--gold), var(--gold-deep));
  }

  .contact {
    position: absolute;
    left: 70px;
    top: 150px;
    width: 400px;
    color: var(--paper-white);
  }
  .contact__name {
    margin: 0;
    font-size: 38px;
    font-weight: 400;
    color: var(--gold);
    font-variant: small-caps;
    letter-spacing: 1px;
    line-height: 1;
  }
  .contact__title {
    margin: 4px 0 22px;
    font-size: 24px;
    font-variant: small-caps;
    line-height: 1;
  }
  .contact__list {
    list-style: none;
    margin: 0;
    padding: 0;
  }
  .contact__item {
    display: flex;
    align-items: flex-start;
    gap: 14px;
    margin-bottom: 10px;
    font-size: 19px;
    text-transform: uppercase;
    line-height: 1.25;
  }
  .contact__item span { font-size: 15px; letter-spacing: 0.3px; }
  .contact__icon {
    flex: 0 0 22px;
    width: 22px;
    height: 22px;
  }

  .brand-name {
    position: absolute;
    margin: 0;
    color: var(--gold);
    font-weight: 600;
    text-align: center;
    line-height: 1.05;
  }
  .card--info .brand-name {
    left: 480px;
    top: 150px;
    width: 320px;
    font-size: 40px;
  }
  .card--brand .brand-name {
    left: 0;
    right: 0;
    top: 190px;
    font-size: 64px;
  }
</style>
</head>
<body>
<main class="canvas">

  <section class="card card--info" aria-label="Business card, contact side">
    <div class="contact">
      <h1 class="contact__name">Nora Beth Quill</h1>
      <p class="contact__title">Owner</p>
      <ul class="contact__list">
        <li class="contact__item">
          <svg class="contact__icon" viewBox="0 0 24 24" aria-hidden="true">
            <path fill="#d8b256" d="M6.6 10.8a15.1 15.1 0 0 0 6.6 6.6l2.2-2.2a1 1 0 0 1 1-.25 11.4 11.4 0 0 0 3.6.57 1 1 0 0 1 1 1V20a1 1 0 0 1-1 1A17 17 0 0 1 3 4a1 1 0 0 1 1-1h3.5a1 1 0 0 1 1 1c0 1.25.2 2.45.57 3.6a1 1 0 0 1-.25 1z"/>
          </svg>
          <span>555-318-4402</span>
        </li>
        <li class="contact__item">
          <svg class="contact__icon" viewBox="0 0 24 24" aria-hidden="true">
            <g fill="none" stroke="#d8b256" stroke-width="1.8">
              <circle cx="12" cy="12" r="9.5"/>
              <ellipse cx="12" cy="12" rx="4.2" ry="9.5"/>
              <line x1="2.5" y1="12" x2="21.5" y2="12"/>
              <path d="M4.5 7h15M4.5 17h15"/>
            </g>
          </svg>
          <span>www.velvetriotrising.com</span>
        </li>
        <li class="contact__item">
          <svg class="contact__icon" viewBox="0 0 24 24" aria-hidden="true">
            <path fill="#d8b256" d="M12 2a7 7 0 0 0-7 7c0 5.25 7 13 7 13s7-7.75 7-13a7 7 0 0 0-7-7zm0 9.5A2.5 2.5 0 1 1 12 6.5a2.5 2.5 0 0 1 0 5z"/>
          </svg>
          <span>1480 E. Harlow Ave, Bldg. 2, &amp; 3,<br>Harrowvale Ca. 95871<br>Fine Vintages &amp; Collectibles</span>
        </li>
      </ul>
    </div>
    <p class="brand-name">Velvet Riot Rising</p>
    <div class="gold-edge"></div>
  </section>

  <section class="card card--brand" aria-label="Business card, brand side">
    <p class="brand-name">Velvet Riot Rising</p>
  </section>

</main>
</body>
</html>
```